KDWB Business Card

Looking for a business card design to incorporate our branding. We want to only use the colors listing in the Branding Package (attached).
Updates

Target Market(s)

People who need their phone or device fixed.

Industry/Entity Type

Electronics

Contact Information for Business Card

Please use:

Brightwick Gadget Clinic LLC
4810 E Harlow Ridge Rd
Suite 417
San Antonio, TX 78163

Marcus Delgrove, Store Manager

(210) 555-0147

Requirements
Must have
• Must include the colors that are contained within the Branding Package PDF file.

```html
<!DOCTYPE html>
<html lang="en">
<head>
<meta charset="utf-8">
<title>Brightwick Gadget Clinic – Business Card</title>
<link rel="stylesheet" href="https://fonts.googleapis.com/css2?family=Arimo:wght@400&display=swap">
<style>
  :root {
    --page: #d9d9d7;
    --silver-light: #f1f0ee;
    --silver-mid: #d6d4d0;
    --silver-dark: #b3b1ad;
    --band-red: #e0502d;
    --band-red-deep: #a8180c;
    --brand-red: #c8361a;
    --brand-orange: #e0583a;
    --ink: #1a1a1a;
    --panel: #1b1b1b;
    --panel-soft: #2c2c2c;
    --warm-text: #d8cdbd;
    --white: #ffffff;
  }
  html, body {
    margin: 0;
    width: 1200px;
    height: 1200px;
    overflow: hidden;
    background: var(--page);
  }
  .card {
    position: absolute;
    left: 100px;
    top: 301px;
    width: 1000px;
    height: 598px;
    overflow: hidden;
    font-family: "Arimo", Arial, sans-serif;
    background: linear-gradient(100deg, var(--silver-light) 0%, var(--silver-mid) 45%, var(--silver-light) 70%, var(--silver-mid) 100%);
    box-shadow: 0 6px 18px rgba(0,0,0,0.25);
  }
  .card-shapes {
    position: absolute;
    inset: 0;
  }
  .brand {
    position: absolute;
    left: 85px;
    top: 130px;
    display: flex;
    align-items: center;
    gap: 18px;
  }
  .brand-square {
    width: 88px;
    height: 88px;
    border-radius: 12px;
    background: var(--brand-orange);
  }
  .brand-name {
    font-size: 40px;
    color: var(--brand-red);
    line-height: 1;
  }
  .holder {
    position: absolute;
    left: 80px;
    top: 304px;
    display: flex;
    align-items: baseline;
    gap: 26px;
    color: var(--white);
  }
  .holder-name { font-size: 46px; }
  .holder-role { font-size: 21px; color: #f6d9cf; }
  .phone {
    position: absolute;
    left: 78px;
    top: 466px;
    display: flex;
    align-items: center;
    gap: 12px;
    font-size: 22px;
    color: var(--warm-text);
    letter-spacing: 0.5px;
  }
  .address {
    position: absolute;
    right: 110px;
    top: 452px;
    text-align: right;
    font-size: 20px;
    line-height: 25px;
    color: var(--warm-text);
    letter-spacing: 0.6px;
  }
  .pin {
    position: absolute;
    right: 74px;
    top: 452px;
  }
</style>
</head>
<body>
  <div class="card">
    <svg class="card-shapes" width="1000" height="598" viewBox="0 0 1000 598">
      <defs>
        <linearGradient id="band-red" x1="0" y1="0" x2="1" y2="0">
          <stop offset="0" stop-color="#e0502d"/>
          <stop offset="0.55" stop-color="#d2401f"/>
          <stop offset="1" stop-color="#a8180c"/>
        </linearGradient>
        <linearGradient id="panel" x1="0" y1="0" x2="1" y2="0">
          <stop offset="0" stop-color="#1b1b1b"/>
          <stop offset="0.45" stop-color="#2e2e2e"/>
          <stop offset="1" stop-color="#181818"/>
        </linearGradient>
      </defs>
      <!-- top strip -->
      <rect class="top-strip" x="0" y="0" width="1000" height="45" fill="#b9b7b3"/>
      <polygon class="top-strip-accent" points="0,0 260,0 210,55 0,55" fill="#c6c4c0"/>
      <!-- dark contact panel -->
      <polygon class="contact-panel" points="700,333 1000,333 1000,536 0,536 0,365 755,365" fill="url(#panel)"/>
      <!-- red name band -->
      <polygon class="name-band" points="0,299 685,299 751,365 0,365" fill="url(#band-red)"/>
      <!-- bottom strips -->
      <rect class="bottom-strip" x="0" y="536" width="1000" height="18" fill="#dcdad6"/>
      <rect class="bottom-strip" x="0" y="554" width="1000" height="44" fill="#bcbab6"/>
    </svg>

    <div class="brand">
      <div class="brand-square"></div>
      <div class="brand-name">Brightwick Gadget Clinic</div>
    </div>

    <div class="holder">
      <span class="holder-name">Marcus Delgrove</span>
      <span class="holder-role">Store Manager</span>
    </div>

    <div class="phone">
      <svg width="16" height="28" viewBox="0 0 16 28" aria-hidden="true">
        <rect x="1.5" y="1.5" width="13" height="25" rx="2" fill="none" stroke="#d8cdbd" stroke-width="2"/>
        <circle cx="8" cy="22.5" r="1.3" fill="#d8cdbd"/>
      </svg>
      <span>(210) 555-0147</span>
    </div>

    <div class="address">
      4810 E Harlow Ridge Rd<br>
      Suite 417, San Antonio, TX 78163
    </div>
    <svg class="pin" width="18" height="26" viewBox="0 0 18 26" aria-hidden="true">
      <path d="M9 1C4.6 1 1 4.5 1 8.9 1 14.6 9 25 9 25s8-10.4 8-16.1C17 4.5 13.4 1 9 1z" fill="#d8cdbd"/>
      <circle cx="9" cy="9" r="3" fill="#1b1b1b"/>
    </svg>
  </div>
</body>
</html>
```